Pet sitting Business needs a website

We need a website that shows our services and prices. Shows our love of animals but also our professionalism. want a gallery, about, blog, services, links to fb and instagram accounts, newsletter archive. want it to be easy to access and wonderful to navigate. want the domain to be Birchfordpawhaven.com
take any info from FB site www.facebook.com/birchfordpawhaven
I would like it to fit square space platform

Target Market(s)

upscale area, responsible pet owners,

Industry/Entity Type

Pet Care

Coding

Coded - Design and coding required

Number of Pages Required

5+ page

Font styles to use
Sans Serif

Requirements
Must have
• (square space platform)
• Menu
• photo gallery
• about us
• services
• policies
• monthly newsletter
• unavailable dates
• Introduction (welcome)
• payment methods
• Daily updates
• testimonials (use from fb site)
Should not have
• stock photos

```html
<!DOCTYPE html>
<html lang="en">
<head>
<meta charset="utf-8">
<title>Birchford Paw Haven</title>
<link href="https://fonts.googleapis.com/css2?family=Open+Sans:wght@400;600;700&display=swap" rel="stylesheet">
<style>
:root{
  --blue:#0f7fab;
  --blue-deep:#0a6e96;
  --gold:#e09a12;
  --gold-dark:#c9860a;
  --ink:#222;
  --muted:#8a8a8a;
  --line:#e2e2e2;
  --dark:#25252c;
  --darker:#1f1f25;
  --white:#fff;
}
*{box-sizing:border-box;margin:0;padding:0}
html,body{width:738px;height:1200px;overflow:hidden;background:var(--white)}
body{font-family:"Open Sans",Arial,sans-serif;color:var(--ink);position:relative}
.header{position:absolute;top:0;left:0;width:738px;height:96px}
.brand{position:absolute;left:82px;top:34px;display:flex;align-items:center;gap:7px}
.brand-dot{width:22px;height:22px;border-radius:50%;background:var(--gold)}
.brand-name{font-size:15px;font-weight:600;color:var(--gold);line-height:1}
.callus{position:absolute;right:82px;top:23px;display:flex;align-items:center;gap:6px}
.callus-text{text-align:right;line-height:1.15}
.callus-text small{display:block;font-size:7px;color:var(--ink)}
.callus-text strong{font-size:10px;font-weight:600;color:var(--gold)}
.callus-icon{width:17px;height:17px;border-radius:50%;background:var(--gold);display:flex;align-items:center;justify-content:center}
.nav{position:absolute;right:82px;top:62px;display:flex;gap:14px;font-size:7.2px}
.nav a{color:var(--ink);text-decoration:none}
.nav a.active{color:var(--blue)}
.hero{position:absolute;top:96px;left:0;width:738px;height:216px;display:grid;grid-template-columns:repeat(5,1fr);grid-template-rows:1fr 1fr}
.hero-photo{border-right:1px solid #fff;border-bottom:1px solid #fff}
.arrow{position:absolute;top:196px;width:15px;height:19px;background:rgba(80,80,80,.6);display:flex;align-items:center;justify-content:center}
.arrow.left{left:0}.arrow.right{right:0}
.intro{position:absolute;top:312px;left:0;width:738px;height:148px;background:var(--blue);text-align:center;color:var(--white)}
.intro h2{font-size:20px;font-weight:600;margin-top:12px}
.intro .lead{font-size:7.6px;font-weight:700;margin-top:5px}
.intro .lead2{font-size:9.6px;font-weight:600;margin-top:1px}
.intro p{font-size:6.4px;line-height:1.8;color:#cfe6f0;width:560px;margin:5px auto 0}
.btn-white{display:inline-block;background:var(--white);color:var(--ink);font-size:6.6px;padding:6px 9px;margin-top:8px}
.services{position:absolute;top:460px;left:0;width:738px;height:248px}
.services h2{text-align:center;color:var(--gold);font-size:20px;font-weight:400;margin-top:21px}
.svc{position:absolute;width:180px;display:flex;gap:7px}
.svc-icon{width:20px;flex:none;display:flex;flex-direction:column;gap:2px}
.svc h3{font-size:12.6px;font-weight:400;color:var(--blue);line-height:1.1}
.svc .price{font-size:7.6px;margin-top:3px}
.svc .note{font-size:6px;color:var(--muted);line-height:1.7;margin-top:4px}
.svc .more{font-size:6px;color:var(--gold)}
.vline{position:absolute;width:1px;background:var(--line);height:60px}
.hline{position:absolute;height:1px;background:var(--line)}
.testimonials{position:absolute;top:708px;left:0;width:738px;height:221px;text-align:center}
.testimonials-bg{position:absolute;inset:0;background:linear-gradient(120deg,#2d2d2d,#4a4a4a 45%,#3a3a3a 70%,#2a2a2a)}
.testimonials-inner{position:relative}
.testimonials h2{color:var(--gold);font-size:15px;font-weight:400;padding-top:19px}
.quote{color:var(--white);font-size:14.5px;line-height:1.75;width:520px;margin:6px auto 0}
.quote b{font-size:20px;font-family:Georgia,serif;vertical-align:-6px}
.cite{color:var(--gold);font-size:9.6px;margin-top:8px}
.avatar{width:52px;height:52px;border-radius:50%;border:2px solid #ddd;background:linear-gradient(#8a8a8a,#b9b9b9);margin:9px auto 0}
.dots{display:flex;gap:4px;justify-content:center;margin-top:14px}
.dots i{width:5px;height:5px;border-radius:50%;background:#bbb}
.dots i.on{background:var(--gold)}
.info{position:absolute;top:929px;left:0;width:738px;height:119px}
.info-col{position:absolute;top:22px;width:290px;text-align:center}
.info-col h2{color:var(--gold);font-size:20px;font-weight:400}
.info-col p{font-size:9.6px;margin-top:2px}
.btn-gold{display:inline-block;background:var(--gold);border:1px solid var(--gold-dark);color:var(--ink);font-size:8px;padding:6px 10px;margin-top:7px}
.btn-grey{display:inline-block;background:#d8d8d8;color:#444;font-size:8px;padding:6px 10px;margin-top:7px}
.info-divider{position:absolute;left:368px;top:12px;width:1px;height:95px;background:var(--line)}
.newsletter{position:absolute;top:1048px;left:0;width:738px;height:39px;background:var(--blue);display:flex;align-items:center;padding-left:111px;gap:6px}
.newsletter h3{color:var(--white);font-size:14.4px;font-weight:700;margin-right:4px;display:flex;align-items:center;gap:4px}
.field{width:118px;height:20px;background:var(--white);font-size:6.4px;color:#999;padding:6px 10px}
.btn-dark{background:var(--darker);color:var(--white);font-size:7.6px;padding:5px 9px}
.footer{position:absolute;top:1087px;left:0;width:738px;height:63px;background:var(--dark);text-align:center;border-bottom:1px solid #3a3a42}
.social{display:flex;gap:16px;justify-content:center;padding-top:14px}
.social i{width:8px;height:8px;border-radius:50%;background:#9a9aa2}
.footnav{font-size:6px;color:#9a9aa2;margin-top:13px;word-spacing:1px}
.bottom{position:absolute;top:1150px;left:0;width:738px;height:50px;background:var(--dark)}
.copy{position:absolute;left:82px;top:21px;font-size:6px;color:#9a9aa2}
.cards{position:absolute;right:82px;top:18px;display:flex;gap:5px}
.cards i{width:20px;height:13px;background:#d8d8dc;border-radius:1px}
</style>
</head>
<body>
<header class="header">
  <div class="brand"><span class="brand-dot"></span><span class="brand-name">Birchford Paw Haven</span></div>
  <div class="callus">
    <div class="callus-text"><small>Call us on</small><strong>555 214 0937</strong></div>
    <div class="callus-icon"><svg width="9" height="9" viewBox="0 0 24 24"><path fill="#fff" d="M6.6 10.8a15 15 0 0 0 6.6 6.6l2.2-2.2c.3-.3.7-.4 1-.2 1.1.4 2.3.6 3.6.6.6 0 1 .4 1 1V20c0 .6-.4 1-1 1A17 17 0 0 1 3 4c0-.6.4-1 1-1h3.5c.6 0 1 .4 1 1 0 1.3.2 2.5.6 3.6.1.3 0 .7-.2 1z"/></svg></div>
  </div>
  <nav class="nav">
    <a class="active">Introduction</a><a>About us</a><a>Services</a><a>Photo Gallery</a><a>Unavailable Dates</a><a>Monthly Newsletter</a><a>Payment Methods</a><a>Policies</a>
  </nav>
</header>

<section class="hero">
  <div class="hero-photo" role="img" aria-label="Small dog portrait" style="background:linear-gradient(135deg,#cfcfcf,#5d5d5d)"></div>
  <div class="hero-photo" role="img" aria-label="Fluffy dog on wooden floor" style="background:linear-gradient(135deg,#c9a574,#8a6a45)"></div>
  <div class="hero-photo" role="img" aria-label="Pet sitter holding a small dog" style="background:linear-gradient(135deg,#9a9a9a,#3e3e3e)"></div>
  <div class="hero-photo" role="img" aria-label="Pet sitter with a black dog" style="background:linear-gradient(135deg,#b45a3a,#6a4a3a)"></div>
  <div class="hero-photo" role="img" aria-label="Black dog by a pool" style="background:linear-gradient(135deg,#a8a8a8,#3a3a3a)"></div>
  <div class="hero-photo" role="img" aria-label="Hen in a garden" style="background:linear-gradient(135deg,#5f7a3a,#7a3a2a)"></div>
  <div class="hero-photo" role="img" aria-label="Two golden dogs" style="background:linear-gradient(135deg,#8a8a8a,#d0d0d0)"></div>
  <div class="hero-photo" role="img" aria-label="Pet sitter with a yellow dog" style="background:linear-gradient(135deg,#c9a06a,#6a7a9a)"></div>
  <div class="hero-photo" role="img" aria-label="Cats resting on a blanket" style="background:linear-gradient(135deg,#e0e0e0,#8a8a8a)"></div>
  <div class="hero-photo" role="img" aria-label="Tortoise on the patio" style="background:linear-gradient(135deg,#6a5a45,#a08060)"></div>
</section>
<div class="arrow left"><svg width="7" height="9" viewBox="0 0 7 9"><path d="M5 1 1.5 4.5 5 8" stroke="#fff" fill="none"/></svg></div>
<div class="arrow right"><svg width="7" height="9" viewBox="0 0 7 9"><path d="M2 1 5.5 4.5 2 8" stroke="#fff" fill="none"/></svg></div>

<section class="intro">
  <h2>Introduction</h2>
  <div class="lead">Now There's A Company That Will Make Sure Your Pet Is Cared For After You Die. Hi my name is Dana Morrow and I would love to introduce myself.</div>
  <div class="lead2">I am a Licensed Veterinarian Technician from Riverton, Ohio.</div>
  <p>Instead of feeling guilty when you must leave your pet for long work days, travel or appointments you can feel good knowing that you have provided your pet with a best friend, Birchford Paw Haven. Birchford Paw Haven provides your pet with one on one attention, plenty of play time and exercise and lots and lots of love until your return. I know pets do better and have less stress when they remain in their own homes where the sites, sounds and smells are familiar.</p>
  <span class="btn-white">Learn More</span>
</section>

<svg width="0" height="0" style="position:absolute"><defs>
  <symbol id="paw" viewBox="0 0 20 18"><ellipse cx="10" cy="12.5" rx="5" ry="4.5" fill="#0f7fab"/><circle cx="3" cy="7" r="2.3" fill="#0f7fab"/><circle cx="7" cy="3" r="2.3" fill="#0f7fab"/><circle cx="13" cy="3" r="2.3" fill="#0f7fab"/><circle cx="17" cy="7" r="2.3" fill="#0f7fab"/></symbol>
</defs></svg>

<section class="services">
  <h2>Services</h2>
  <div class="svc" style="left:81px;top:62px"><div class="svc-icon"><svg width="18" height="16"><use href="#paw"/></svg><svg width="18" height="16"><use href="#paw"/></svg></div><div><h3>Daily Visit</h3><div class="price">$25.00(per visit)</div><div class="note">No additional charge for each pet<br>Dog walks or play time for your pet</div><div class="more">More</div></div></div>
  <div class="svc" style="left:296px;top:62px"><div class="svc-icon"><svg width="18" height="16"><use href="#paw"/></svg><svg width="18" height="16"><use href="#paw"/></svg></div><div><h3>Just walks</h3><div class="price">$15.00/ 20 min walk</div><div class="note">No additional charge for each pet<br>Dog walks or play time for your pet</div><div class="more">More</div></div></div>
  <div class="svc" style="left:520px;top:62px"><div class="svc-icon"><svg width="18" height="16"><use href="#paw"/></svg><svg width="18" height="16"><use href="#paw"/></svg></div><div><h3>Pet Taxi</h3><div class="price">Grooming, vet drop off/pic up</div><div class="note">No additional charge for each pet<br>Dog walks or play time for your pet</div><div class="more">More</div></div></div>
  <div class="svc" style="left:81px;top:155px"><div class="svc-icon"><svg width="18" height="16"><use href="#paw"/></svg><svg width="18" height="16"><use href="#paw"/></svg></div><div><h3>Potty visits</h3><div class="price">$10.00</div><div class="note">No additional charge for each pet<br>Dog walks or play time for your pet</div><div class="more">More</div></div></div>
  <div class="svc" style="left:296px;top:155px"><div class="svc-icon"><svg width="18" height="16"><use href="#paw"/></svg><svg width="18" height="16"><use href="#paw"/></svg></div><div><h3>Medication</h3><div class="price">Injections or subcutaneous fluids<br>$5 per administration</div><div class="note">No additional charge for each pet</div><div class="more">More</div></div></div>
  <div class="svc" style="left:520px;top:155px"><div class="svc-icon"><svg width="18" height="16"><use href="#paw"/></svg><svg width="18" height="16"><use href="#paw"/></svg></div><div><h3>Dog park</h3><div class="price">30 min of play $40</div><div class="note">No additional charge for each pet<br>Dog walks or play time for your pet</div><div class="more">More</div></div></div>
  <div class="vline" style="left:252px;top:64px"></div><div class="vline" style="left:483px;top:64px"></div>
  <div class="vline" style="left:252px;top:157px"></div><div class="vline" style="left:483px;top:157px"></div>
  <div class="hline" style="left:81px;top:141px;width:134px"></div>
  <div class="hline" style="left:297px;top:141px;width:149px"></div>
  <div class="hline" style="left:521px;top:141px;width:135px"></div>
</section>

<section class="testimonials">
  <div class="testimonials-bg" role="img" aria-label="Dog playing with its owner in a park"></div>
  <div class="testimonials-inner">
    <h2>Testimonials</h2>
    <p class="quote"><b>“</b> Praesent porta tortor dolor, quis maximus tortor pretium et. Prae sent eget vulputate risus. Suspendisse dignissim. <b>”</b></p>
    <div class="cite">- Mark Ellery, City</div>
    <div class="avatar" role="img" aria-label="Customer portrait"></div>
    <div class="dots"><i class="on"></i><i></i><i></i><i></i></div>
  </div>
</section>

<section class="info">
  <div class="info-col" style="left:80px"><h2>Policies</h2><p>Nunc risus libero, cursus at dictum nec.</p><span class="btn-gold">View Our Policies</span></div>
  <div class="info-divider"></div>
  <div class="info-col" style="left:368px"><h2>Unavailable Dates</h2><p>May 6-8th &nbsp; | &nbsp; MAY 21-23 &nbsp; | &nbsp; July 3-16</p><span class="btn-grey">Read more</span></div>
</section>

<section class="newsletter">
  <h3><svg width="14" height="11" viewBox="0 0 14 11"><rect x="1" y="1" width="12" height="9" fill="none" stroke="#fff" stroke-width="1.4"/><path d="M1 1.5 7 6l6-4.5" fill="none" stroke="#fff" stroke-width="1.4"/></svg>NEWSLETTER SUBSCRIBE</h3>
  <div class="field">Name</div><div class="field">Email</div><div class="btn-dark">Subscribe</div>
</section>

<footer class="footer">
  <div class="social"><i></i><i></i><i></i><i></i><i></i></div>
  <div class="footnav">Introduction &nbsp;| &nbsp;About us &nbsp;| &nbsp;Services &nbsp;| &nbsp;Photo Gallery &nbsp;| &nbsp;Unavailable Dates &nbsp;| &nbsp;Monthly Newsletter &nbsp;| &nbsp;Payment Methods &nbsp;| &nbsp;Policies</div>
</footer>
<div class="bottom">
  <div class="copy">Copyright © 2016 Birchford Paw Haven. All rights reserved.</div>
  <div class="cards"><i></i><i></i><i></i><i></i></div>
</div>
</body>
</html>
```